Business Card Design

we are a small based family business that specialise in 12v led lights for velmora caravans.
we also sell 12v switches, wire, circuit breakers, dimmers etc but our main line is LEDs.
We would like something that reflects the LED lighting on our cards.
www.ridgeglowleds.com.au is where you can have a look at to get ideas, of our product.
I have attached the logo we generally use on all our tradix listings and is the main header on our website.

Look forward to seeing what your team comes up with.

Industry/Entity Type

Business

Contact Information for Business Card

Tam 0438 207 915
Quorrin Vale QLD 4399

www.ridgeglowleds.com

```html
<!DOCTYPE html>
<html lang="en">
<head>
<meta charset="utf-8">
<title>Ridge Glow LEDs – Business Card</title>
<link rel="stylesheet" href="https://fonts.googleapis.com/css2?family=Orbitron:wght@400;700;900&display=swap">
<style>
  :root {
    --bg: #6e6e6e;
    --card-white: #ffffff;
    --card-shade: #e9e9e9;
    --brand-red: #a32b12;
    --ink: #111111;
    --ink-soft: #333333;
  }
  * { margin: 0; padding: 0; box-sizing: border-box; }
  html, body { width: 1200px; height: 750px; overflow: hidden; }
  body {
    background: var(--bg);
    font-family: "Orbitron", sans-serif;
    position: relative;
  }
  .card {
    position: absolute;
    width: 490px;
    height: 280px;
    overflow: hidden;
    box-shadow: 0 6px 18px rgba(0,0,0,.35);
  }
  .card--front {
    left: 90px; top: 60px;
    background: radial-gradient(ellipse at 55% 40%, var(--card-white) 30%, var(--card-shade) 100%);
    display: flex; align-items: center; justify-content: center;
  }
  .card--back { left: 620px; top: 60px; background: var(--brand-red); }
  .card--details {
    left: 355px; top: 410px;
    background: radial-gradient(ellipse at 40% 35%, var(--card-white) 40%, var(--card-shade) 100%);
  }
  .brand-name {
    font-weight: 900;
    color: var(--brand-red);
    text-transform: uppercase;
    letter-spacing: .5px;
    line-height: 1;
  }
  .card--front .brand-name { font-size: 30px; }
  .card--details .brand-name {
    position: absolute; left: 24px; top: 34px; font-size: 21px;
  }
  .base-band {
    position: absolute; left: 0; right: 0; bottom: 0;
    height: 44px;
    background: var(--brand-red);
  }
  .person {
    position: absolute; right: 26px; top: 30px; text-align: right;
  }
  .person__name { color: var(--brand-red); font-size: 12px; font-weight: 400; letter-spacing: .5px; }
  .person__role { color: var(--ink); font-size: 8px; letter-spacing: .5px; margin-top: 3px; }
  .website {
    position: absolute; right: 26px; top: 112px;
    font-size: 9px; color: var(--ink-soft); letter-spacing: .3px;
  }
  .contact {
    position: absolute; left: 24px; top: 86px;
    list-style: none; font-size: 8.5px; color: var(--ink-soft);
  }
  .contact__address { line-height: 1.5; margin-bottom: 8px; }
  .contact__line { display: flex; align-items: center; gap: 7px; height: 16px; }
  .contact__icon { width: 9px; height: 9px; flex: none; }
</style>
</head>
<body>

  <section class="card card--front" aria-label="Card front">
    <span class="brand-name">Ridge Glow LEDs</span>
  </section>

  <section class="card card--back" aria-label="Card reverse"></section>

  <section class="card card--details" aria-label="Card contact side">
    <div class="base-band" aria-hidden="true"></div>

    <span class="brand-name">Ridge Glow LEDs</span>

    <div class="person">
      <p class="person__name">CORIN MADDOCK</p>
      <p class="person__role">FINANCIAL ADVISOR</p>
    </div>

    <p class="website">www.ridgeglowleds.com</p>

    <ul class="contact">
      <li class="contact__address">14 Larkspur Lane<br>Quorrin Vale</li>
      <li class="contact__line">
        <svg class="contact__icon" viewBox="0 0 10 10" aria-hidden="true"><path d="M2,0.5 L4,2.5 L3,3.8 Q4.5,6 6.2,7 L7.5,6 L9.5,8 L8,9.5 Q3,9 0.5,2 Z" fill="var(--brand-red)"/></svg>
        012 345 6789
      </li>
      <li class="contact__line">
        <svg class="contact__icon" viewBox="0 0 10 10" aria-hidden="true"><rect x="2.5" y="0.5" width="5" height="9" rx="1" fill="none" stroke="var(--brand-red)" stroke-width="1.2"/></svg>
        012 345 6789
      </li>
      <li class="contact__line">
        <svg class="contact__icon" viewBox="0 0 10 10" aria-hidden="true"><rect x="3" y="0.5" width="4" height="3" fill="var(--brand-red)"/><rect x="0.5" y="4" width="9" height="5.5" fill="var(--brand-red)"/></svg>
        012 345 6789
      </li>
      <li class="contact__line">
        <svg class="contact__icon" viewBox="0 0 10 10" aria-hidden="true"><rect x="0.5" y="2" width="9" height="6" fill="var(--brand-red)"/><path d="M0.5,2 L5,5.5 L9.5,2" fill="none" stroke="var(--card-white)" stroke-width="0.8"/></svg>
        hello@ridgeglowleds.com
      </li>
    </ul>
  </section>

</body>
</html>
```